Dynamic Business Card for Sports Supplements Company

Hi! I'm looking for an awesome business card to match my existing sports supplement company. I have uploaded my current company logo and screenshot of the front page of my website.

I would like to have something dynamic and interesting and utilize the colors in the website - the reds and purples

The business card should be double sided and focus on a unique eye-catching design on the back and include all the relevant company info.

Most importantly, it should say somewhere: "Sign up on our website for a coupon code."

Target Market(s)

Mostly for women gym goers but it shouldn't be too feminine. It should be in keeping with the website design. It should flow and clearly be connected to it

Industry/Entity Type

Business

Contact Information for Business Card

Lorraine K. Vestal
CEO
LVestal@Quorvanexco.com
www.quorvanexco.com
555.417.3820
P.O. Box 47315
Halden, Oregon 00000

Sign up on our website for a coupon code

Font styles to use
Serif
Sans Serif
Other font styles liked:
• Novecento font family and "Quorvanex" is in AR Destine font

Requirements
Must have
• One side should be a bold Quorvanex logo design. Even just the symbol itself may be o.k. (see attached file)

```html
<!DOCTYPE html>
<html lang="en">
<head>
<meta charset="utf-8">
<title>Quorvanex Business Card</title>
<link rel="stylesheet" href="https://fonts.googleapis.com/css2?family=Roboto:wght@400;500&family=Russo+One&display=swap">
<style>
  :root {
    --bg: #e9e6e1;
    --black: #111111;
    --black-soft: #262626;
    --red: #e3202b;
    --red-light: #f0414a;
    --red-dark: #c9141f;
    --white: #ffffff;
    --grey: #cfcfcf;
  }
  * { margin: 0; padding: 0; box-sizing: border-box; }
  html, body { width: 1200px; height: 950px; overflow: hidden; background: var(--bg); }
  body { font-family: "Roboto", Arial, sans-serif; position: relative; }

  .card {
    position: absolute;
    left: 250px;
    width: 700px;
    height: 400px;
    overflow: hidden;
    box-shadow: 0 14px 30px rgba(0,0,0,0.25);
  }
  .card-front { top: 50px; background: linear-gradient(135deg, var(--black-soft) 0%, var(--black) 55%); }
  .card-back { top: 500px; background: linear-gradient(135deg, var(--red-dark) 0%, var(--red) 45%, var(--red-light) 100%); }

  .brand { position: absolute; text-align: center; color: var(--white); }
  .brand-mark { display: inline-block; width: 30px; height: 30px; background: var(--red); vertical-align: middle; margin-right: 12px; }
  .brand-name { font-family: "Russo One", Arial, sans-serif; text-transform: uppercase; vertical-align: middle; letter-spacing: 1px; }
  .brand-tagline { display: block; font-size: 11px; letter-spacing: 3px; text-transform: uppercase; margin-top: 6px; }

  .card-front .brand { right: 60px; top: 70px; width: 280px; }
  .card-front .brand-name { font-size: 34px; }

  .divider { position: absolute; right: 40px; top: 180px; width: 300px; height: 1px; background: var(--grey); opacity: 0.7; }

  .address { position: absolute; right: 60px; top: 200px; width: 220px; color: var(--white); font-size: 17px; font-style: normal; line-height: 1.5; text-align: left; }

  .web-band { position: absolute; right: 0; bottom: 0; width: 100%; height: 48px; }
  .web-band svg { position: absolute; inset: 0; width: 100%; height: 100%; }
  .web-url { position: absolute; right: 60px; bottom: 13px; color: var(--white); font-size: 17px; font-weight: 500; letter-spacing: 1.5px; }

  .contact { position: absolute; left: 50px; top: 200px; color: var(--white); }
  .contact-name { color: var(--red); font-size: 28px; font-weight: 400; }
  .contact-title { font-size: 16px; margin: 4px 0 16px; }
  .contact-line { display: flex; align-items: center; gap: 10px; font-size: 16px; margin-bottom: 6px; }
  .contact-line svg { width: 16px; height: 16px; flex: none; }

  .card-back .brand { left: 0; right: 0; top: 120px; }
  .card-back .brand-mark { width: 48px; height: 48px; background: var(--white); margin-right: 18px; }
  .card-back .brand-name { font-size: 62px; }
  .card-back .brand-tagline { font-size: 14px; letter-spacing: 5px; margin-top: 10px; }
  .coupon { position: absolute; left: 0; right: 0; top: 290px; text-align: center; color: var(--white); font-size: 19px; font-style: italic; letter-spacing: 0.5px; }
</style>
</head>
<body>
  <section class="card card-front">
    <div class="brand">
      <span class="brand-mark"></span><span class="brand-name">Quorvanex</span>
      <span class="brand-tagline">Strength In Every Step</span>
    </div>
    <div class="divider"></div>
    <address class="address">
      P.O. Box 47315<br>Halden, Oregon 00000
    </address>

    <div class="contact">
      <h1 class="contact-name">Lorraine K. Vestal</h1>
      <p class="contact-title">CEO</p>
      <p class="contact-line">
        <svg viewBox="0 0 16 16" aria-hidden="true"><path fill="#e3202b" d="M3 1h3l1.5 4-2 1.3a9 9 0 0 0 4.2 4.2L11 8.5l4 1.5v3a2 2 0 0 1-2 2A12 12 0 0 1 1 3a2 2 0 0 1 2-2z"/></svg>
        555.417.3820
      </p>
      <p class="contact-line">
        <svg viewBox="0 0 16 16" aria-hidden="true"><rect x="1" y="3" width="14" height="10" fill="#e3202b"/><path d="M1 3l7 6 7-6" fill="none" stroke="#111" stroke-width="1.3"/></svg>
        LVestal@Quorvanexco.com
      </p>
    </div>

    <div class="web-band">
      <svg viewBox="0 0 700 48" preserveAspectRatio="none" aria-hidden="true">
        <polygon points="340,0 700,0 700,48 300,48" fill="#e3202b"/>
      </svg>
      <span class="web-url">www.quorvanexco.com</span>
    </div>
  </section>

  <section class="card card-back">
    <div class="brand">
      <span class="brand-mark"></span><span class="brand-name">Quorvanex</span>
      <span class="brand-tagline">Strength In Every Step</span>
    </div>
    <p class="coupon">Sign up on our website for a coupon code</p>
  </section>
</body>
</html>
```